Web Developer Needs a Business Card Design

I need a personal business card design that represents me as a web developer for potential employers. I would like the background to be a dark color on the front for contrast with my logo and name. The back will have all my information along with a smaller version of the logo. I want something with a modern look and feel, not too conservative. This will be used for potential employers and freelance work.

Industry/Entity Type

Business

Contact Information for Business Card

Front should have my logo and name. The back should have all my personal information which would include: name: Tom Varulek, phone: 570-614-3098, email: tomvarulek@quillbox.net, website url: www.tomvarulek.net, logo, web developer.

Font styles to use
Sans Serif

Requirements
Must have
• Must include my logo. The color palette base color will be the logo color.

```html
<!DOCTYPE html>
<html lang="en">
<head>
<meta charset="utf-8">
<title>Tom Varulek — Business Card</title>
<link rel="stylesheet" href="https://fonts.googleapis.com/css2?family=Open+Sans:wght@400;600&display=swap">
<style>
  :root {
    --teal: #44cdb0;
    --ink: #030303;
    --paper-light: #f1f1f1;
    --paper-mid: #cfcfcf;
    --backdrop: #d9d9d9;
    --white: #f4f4f4;
    --rule: #8a8a8a;
  }
  * { margin: 0; padding: 0; box-sizing: border-box; }
  html, body { width: 1189px; height: 1200px; overflow: hidden; }
  body {
    background: var(--backdrop);
    font-family: "Open Sans", sans-serif;
    position: relative;
  }
  .card {
    position: absolute;
    left: 140px;
    width: 918px;
    height: 524px;
    background: var(--ink);
    overflow: hidden;
  }
  .card--back { top: 45px; }
  .card--front { top: 623px; }

  /* Back side */
  .back__header {
    position: absolute; left: 0; top: 0; width: 100%; height: 245px;
    background: radial-gradient(ellipse at 50% 100%, var(--paper-light) 0%, var(--paper-mid) 90%);
    display: flex; align-items: center; justify-content: center; gap: 18px;
  }
  .brand-mark {
    width: 56px; height: 56px; border-radius: 50%;
    border: 7px solid var(--teal);
  }
  .brand-name {
    color: var(--teal); font-weight: 600; font-size: 40px; letter-spacing: 0.5px;
  }
  .back__band {
    position: absolute; left: 0; top: 249px; width: 100%; height: 23px;
    background: var(--teal);
  }
  .back__rule {
    position: absolute; left: 0; top: 276px; width: 100%; height: 1px;
    background: var(--rule);
  }
  .identity {
    position: absolute; right: 552px; top: 330px; text-align: right;
  }
  .identity__name {
    color: var(--teal); font-weight: 600; font-size: 40px; line-height: 1.1;
  }
  .identity__role {
    color: var(--white); font-weight: 400; font-size: 28px; margin-top: 6px;
  }
  .divider {
    position: absolute; left: 433px; top: 308px; width: 2px; height: 176px;
    background: var(--rule);
  }
  .contacts {
    position: absolute; left: 462px; top: 334px; list-style: none;
  }
  .contacts__item {
    display: flex; align-items: center; gap: 24px;
    color: var(--white); font-size: 28px; height: 43px;
  }
  .contacts__icon { width: 22px; height: 22px; flex: none; }

  /* Front side */
  .front__mark {
    position: absolute; left: 340px; top: 111px; width: 236px; height: 236px;
    border-radius: 50%; border: 9px solid var(--teal);
  }
  .front__name {
    position: absolute; left: 0; width: 100%; top: 395px; text-align: center;
    color: var(--teal); font-weight: 600; font-size: 50px;
  }
</style>
</head>
<body>
  <section class="card card--back">
    <div class="back__header">
      <span class="brand-mark" aria-hidden="true"></span>
      <span class="brand-name">Tom Varulek</span>
    </div>
    <div class="back__band"></div>
    <div class="back__rule"></div>

    <div class="identity">
      <p class="identity__name">Tom Varulek</p>
      <p class="identity__role">web developer</p>
    </div>

    <div class="divider"></div>

    <ul class="contacts">
      <li class="contacts__item">
        <svg class="contacts__icon" viewBox="0 0 22 22" aria-hidden="true">
          <rect width="22" height="22" rx="2" fill="var(--teal)"/>
          <path d="M7 4 L10 7 L8.5 9 Q10 13 13 14.5 L15 13 L18 16 L16 18 Q9 17 5 7 Z" fill="var(--ink)"/>
        </svg>
        <span>570-614-3098</span>
      </li>
      <li class="contacts__item">
        <svg class="contacts__icon" viewBox="0 0 22 22" aria-hidden="true">
          <rect width="22" height="22" rx="2" fill="var(--teal)"/>
          <circle cx="11" cy="11" r="7" fill="none" stroke="var(--ink)" stroke-width="2"/>
          <path d="M4 11 H18 M11 4 Q7 11 11 18 M11 4 Q15 11 11 18" fill="none" stroke="var(--ink)" stroke-width="1.4"/>
        </svg>
        <span>www.tomvarulek.net</span>
      </li>
      <li class="contacts__item">
        <svg class="contacts__icon" viewBox="0 0 22 22" aria-hidden="true">
          <rect width="22" height="22" rx="2" fill="var(--teal)"/>
          <rect x="4" y="6" width="14" height="10" fill="none" stroke="var(--ink)" stroke-width="1.6"/>
          <path d="M4 6 L11 12 L18 6" fill="none" stroke="var(--ink)" stroke-width="1.6"/>
        </svg>
        <span>tomvarulek@quillbox.net</span>
      </li>
    </ul>
  </section>

  <section class="card card--front">
    <span class="front__mark" aria-hidden="true"></span>
    <p class="front__name">Tom Varulek</p>
  </section>
</body>
</html>
```